RTavenor Business Cards & Letterhead

I have a logo but need a design for some new business cards. We are a Design-Build Firm that specializes in the design and construction of commercial projects.
the cards need to be professional. no cartoon stuff.
i would like to have the cards in AI format so I can update the card as needed. Logo is provided.
Our Address is: 4187 Marlowe Ct. Larkfield, Vermont 27614

```html
<!DOCTYPE html>
<html lang="en">
<head>
<meta charset="utf-8">
<title>RTavenor Business Cards</title>
<link href="https://fonts.googleapis.com/css2?family=Open+Sans:wght@400;600;700&display=swap" rel="stylesheet">
<style>
  :root {
    --stage: #2a2a2d;
    --card: #1e1e22;
    --blue: #1a82c8;
    --blue-deep: #0b4f86;
    --grey: #8a8a8e;
    --white: #f2f2f2;
  }
  * { box-sizing: border-box; margin: 0; padding: 0; }
  html, body { width: 1200px; height: 780px; overflow: hidden; }
  body {
    background: var(--stage);
    font-family: "Open Sans", Arial, sans-serif;
    position: relative;
  }
  .card {
    position: absolute;
    top: 240px;
    width: 520px;
    height: 300px;
    border-radius: 18px;
    background: var(--card);
    overflow: hidden;
    box-shadow: 0 12px 30px rgba(0,0,0,.45);
  }
  .card-back { left: 50px; }
  .card-front { left: 630px; }

  .brand {
    position: absolute;
    display: flex;
    align-items: center;
    gap: 10px;
    color: var(--grey);
    font-weight: 700;
    letter-spacing: 1px;
    white-space: nowrap;
  }
  .brand-mark { background: var(--blue); border-radius: 3px; }
  .card-back .brand {
    left: 50%; top: 50%;
    transform: translate(-50%, -50%);
    font-size: 52px;
  }
  .card-back .brand-mark { width: 38px; height: 38px; }
  .card-front .brand { left: 30px; top: 112px; font-size: 30px; }
  .card-front .brand-mark { width: 22px; height: 22px; }

  .wave { position: absolute; inset: 0; }

  .holder {
    position: absolute;
    right: 34px; top: 26px;
    text-align: right;
  }
  .holder-name { color: var(--blue); font-weight: 700; font-size: 20px; letter-spacing: .5px; }
  .holder-role { color: var(--white); font-size: 13px; font-weight: 600; }
  .corner-tab {
    position: absolute;
    right: 0; top: 24px;
    width: 18px; height: 46px;
    background: var(--blue);
  }

  .address {
    position: absolute;
    left: 88px; top: 168px;
    color: var(--white);
    font-size: 12.5px;
    line-height: 17px;
  }
  .contacts {
    position: absolute;
    left: 62px; top: 212px;
    list-style: none;
    color: var(--white);
    font-size: 12.5px;
    line-height: 19px;
  }
  .contacts li { display: flex; align-items: center; gap: 8px; }
  .contacts svg { width: 13px; height: 13px; flex: none; }
</style>
</head>
<body>

<section class="card card-back">
  <div class="brand"><span class="brand-mark"></span>RTAVENOR</div>
</section>

<section class="card card-front">
  <svg class="wave" viewBox="0 0 520 300" aria-hidden="true">
    <defs>
      <linearGradient id="waveFill" x1="0" y1="1" x2="1" y2="0">
        <stop offset="0" stop-color="#0b4f86"/>
        <stop offset=".55" stop-color="#1a82c8"/>
        <stop offset="1" stop-color="#0b4f86"/>
      </linearGradient>
    </defs>
    <path d="M150 300 C300 285 345 230 365 150 C378 100 400 88 440 84 L520 76 L520 300 Z" fill="url(#waveFill)"/>
    <path d="M140 288 C235 292 300 265 340 205 C310 258 245 284 150 296 Z" fill="#8a8a8e"/>
  </svg>

  <span class="corner-tab"></span>
  <div class="holder">
    <p class="holder-name">REID TAVENOR</p>
    <p class="holder-role">Founder/President</p>
  </div>

  <div class="brand"><span class="brand-mark"></span>RTAVENOR</div>

  <p class="address">4187 Marlowe Ct. Larkfield,<br>Vermont 27614</p>

  <ul class="contacts">
    <li>
      <svg viewBox="0 0 16 16"><circle cx="8" cy="8" r="8" fill="#1a82c8"/><path d="M5 4.5l1.6-.5 1 2-1 .8a5 5 0 0 0 2.6 2.6l.8-1 2 1-.5 1.6c-3.5.3-6.8-3-6.5-6.5z" fill="#fff"/></svg>
      (802) 555-0148
    </li>
    <li>
      <svg viewBox="0 0 16 16"><circle cx="8" cy="8" r="8" fill="#1a82c8"/><circle cx="8" cy="8" r="4.5" fill="none" stroke="#fff"/><path d="M3.5 8h9M8 3.5c-2 2.5-2 6.5 0 9M8 3.5c2 2.5 2 6.5 0 9" fill="none" stroke="#fff" stroke-width=".8"/></svg>
      www.rtavenor.com
    </li>
    <li>
      <svg viewBox="0 0 16 16"><circle cx="8" cy="8" r="8" fill="#1a82c8"/><rect x="4" y="5" width="8" height="6" fill="none" stroke="#fff"/><path d="M4 5l4 3.5L12 5" fill="none" stroke="#fff"/></svg>
      RLT@RTavenor.com
    </li>
  </ul>
</section>

</body>
</html>
```